Powerpoint Design for AI Consulting Company

Description
Velmora Quill Industries is a consulting and technology company that engineers AI transformations, automation, and decision intelligence for financial firms, mining companies, and supply chains.
We already have a logo and brand colors (see attached). We need a professional, modern PowerPoint template that reflects our brand identity and positioning.
Key Requirements
Use our logo and color palette (deep blue, orange, white/black backgrounds).
Clean, modern design with subtle technology-inspired elements (data flows, AI networks, abstract systems).
Must feel sophisticated, bold, and boardroom-ready for executive presentations.
Templates should support both dark and light backgrounds.
Deliverables
A reusable PowerPoint template (.PPTX) with at least these layouts:
Title / Cover slide – dramatic, logo placement, tagline space.
Agenda slide – clean, structured layout.
Section divider slides – strong use of brand colors.
Content slides – text + image, text + icon.
Charts & data slides – bar, line, pie, comparison table, infographics.
Case study / example project slide. - ROI / Transformation Journey
Timeline / roadmap slide.
Team profile slide.
Reframe Slide – A provocative insight that reframes the client’s current thinking.
Options & Trade-offs Slide – Matrix showing different paths and consequences.
Execution Roadmap Slide – Step-by-step phased implementation view.
Closing / thank-you slide with contact details.
Style Guide
Colors: Primary – deep blue (#0D3559), Secondary – orange (#E87722), Accents – silver/white.
Fonts: Modern sans-serif (e.g., Montserrat, Lato, or similar).
Visual elements: Abstract technology, data-inspired graphics, mathematical motifs. Avoid clutter or overly “sci-fi” looks.
Tone: Premium consulting + innovative AI firm.
Target Market(s)
Velmora Quill Industries’ target market is senior decision-makers in finance, mining, and supply chains, where complexity, risk, and ROI pressure are high. Primary buyers include family offices, boutique wealth managers, super funds, and mining/supply chain executives, who value insight-driven strategies, automation, and decision intelligence. A secondary market includes professional services (accounting, legal, medical) and regulated SMEs (daycare, aged care, community services) burdened by admin and compliance. The slide deck must appeal to a boardroom audience — authoritative, data-driven, and visually clean — while remaining flexible enough to adapt for SME professional services.
Look and feel
Each slider illustrates characteristics of the customer's brand and the style your logo design should communicate.

```html
<!DOCTYPE html>
<html lang="en">
<head>
<meta charset="utf-8">
<title>Velmora Quill Industries — Presentation Template</title>
<link rel="stylesheet" href="https://fonts.googleapis.com/css2?family=Outfit:wght@300;400;500;600;700;800&display=swap">
<style>
:root{
  --blue-deep:#0d3559;
  --blue-mid:#123f6e;
  --blue-dark:#0b2a4a;
  --orange:#e87722;
  --white:#ffffff;
  --silver:#c9d3de;
  --card:rgba(255,255,255,0.06);
  --line:rgba(255,255,255,0.85);
}
*{margin:0;padding:0;box-sizing:border-box}
html,body{width:1002px;height:1200px;overflow:hidden;background:#fff}
body{font-family:"Outfit",sans-serif;color:var(--white);position:relative}
.slide{position:absolute;width:466px;height:262px;overflow:hidden;
  background:radial-gradient(ellipse at 100% 100%,rgba(120,85,60,.45),transparent 55%),
             radial-gradient(ellipse at 0% 0%,rgba(90,80,80,.35),transparent 45%),
             linear-gradient(135deg,var(--blue-mid),var(--blue-deep) 60%,var(--blue-dark));}
.slide--cover{left:25px;top:31px;background:radial-gradient(ellipse at 35% 0%,#1f5a8c,transparent 55%),radial-gradient(ellipse at 90% 70%,rgba(30,90,170,.55),transparent 50%),linear-gradient(160deg,#174a7a,var(--blue-deep))}
.slide--agenda{left:511px;top:31px}
.slide--solutions{left:25px;top:321px}
.slide--why{left:511px;top:321px}
.slide--compare{left:25px;top:611px}
.slide--path{left:511px;top:611px}
.slide--roadmap{left:25px;top:898px}
.slide--thanks{left:511px;top:898px;background:radial-gradient(ellipse at 10% 40%,rgba(30,90,170,.5),transparent 45%),linear-gradient(160deg,#174a7a,var(--blue-deep))}
.abs{position:absolute}
.title{position:absolute;left:17px;top:16px;font-size:11.5px;font-weight:500;white-space:nowrap}
.title em{font-style:normal;color:var(--orange)}
.title::after{content:"";display:inline-block;width:15px;height:1px;background:var(--white);margin-left:7px;vertical-align:middle}
.brandmark{position:absolute;right:17px;top:18px;font-size:7px;font-weight:600;letter-spacing:.04em;line-height:1.05;text-align:right;color:var(--white)}
.page{position:absolute;right:17px;bottom:10px;font-size:7.5px;font-weight:600}
/* cover */
.cover-logo{position:absolute;left:0;right:0;top:58px;text-align:center;font-size:17px;font-weight:600;line-height:1.15;color:var(--white)}
.cover-logo small{display:block;font-size:6.5px;font-weight:500;letter-spacing:.08em;margin-top:3px}
.cover-name{position:absolute;left:0;right:0;top:143px;text-align:center;font-size:9.5px;font-weight:400}
.cover-tag{position:absolute;left:0;right:0;top:172px;text-align:center;font-size:15px;font-weight:500;color:var(--orange);line-height:27px}
/* agenda */
.agenda-card{position:absolute;width:185px;height:56px;background:var(--card);border-radius:5px}
.agenda-num{position:absolute;left:10px;top:16px;width:24px;height:24px;background:var(--orange);border-radius:2px;font-size:9px;font-weight:600;display:flex;align-items:center;justify-content:center}
.agenda-head{position:absolute;left:51px;top:9px;font-size:7.6px;font-weight:500;color:var(--orange);white-space:nowrap}
.agenda-text{position:absolute;left:51px;top:23px;font-size:6.8px;line-height:14px;width:130px}
/* solutions */
.sub{position:absolute;left:17px;top:42px;font-size:7.2px;font-weight:600}
/* why */
.why-sub{position:absolute;left:21px;top:48px;font-size:8.6px;font-weight:600}
.why-list{position:absolute;left:30px;top:72px;width:186px;list-style:none}
.why-list li{font-size:8px;line-height:18.5px;margin-bottom:7px;position:relative;padding-left:10px}
.why-list li::before{content:"";position:absolute;left:0;top:7px;width:3px;height:3px;border-radius:50%;background:var(--orange)}
.why-list b{font-weight:400;color:var(--orange)}
.why-photo{position:absolute;left:259px;top:54px;width:183px;height:167px;border-radius:8px;border-left:2px solid var(--orange);border-bottom:2px solid var(--orange);
  background:radial-gradient(circle at 50% 50%,rgba(200,220,255,.5),transparent 30%),linear-gradient(135deg,#8a5a35,#b07845 45%,#5b4a3e)}
/* compare */
.compare-title{position:absolute;left:0;right:0;top:33px;display:flex;justify-content:center;align-items:center;gap:10px;font-size:11.5px;font-weight:500}
.compare-title::before,.compare-title::after{content:"";width:15px;height:1px;background:var(--white)}
.compare-title em{font-style:normal;color:var(--orange)}
.compare-table{position:absolute;left:37px;top:70px;width:393px;border-collapse:collapse;border-radius:7px;overflow:hidden;background:rgba(255,255,255,.04)}
.compare-table th,.compare-table td{text-align:left;padding-left:21px;font-size:8px;border-left:1px solid rgba(255,255,255,.1)}
.compare-table th:first-child,.compare-table td:first-child{border-left:none}
.compare-table th{height:31px;color:var(--orange);font-weight:600;font-size:8.6px;border-bottom:1px solid rgba(255,255,255,.12)}
.compare-table td{height:28px;font-weight:400}
.compare-table tr:nth-child(even) td{background:rgba(255,255,255,.06)}
/* path */
.step{position:absolute;width:110px;text-align:center;transform:translateX(-50%)}
.step-head{font-size:6.8px;font-weight:500;color:var(--orange);white-space:nowrap}
.step-text{font-size:6.2px;line-height:13px;margin-top:4px}
/* roadmap */
.tl{position:absolute;width:64px;margin-left:-32px;text-align:center}
.tl-year{font-size:6.8px;color:var(--orange);font-weight:500;line-height:10px}
.tl-text{font-size:5px;line-height:9px;margin-top:2px;white-space:nowrap}
/* thanks */
.thanks-logo{position:absolute;left:0;right:0;top:52px;text-align:center;font-size:17px;font-weight:600;line-height:1.1}
.thanks-logo small{display:block;font-size:6.5px;font-weight:500;letter-spacing:.08em;margin-top:3px}
.thanks-big{position:absolute;left:0;right:0;top:115px;text-align:center;font-size:41px;font-weight:800;letter-spacing:-.01em}
.thanks-big em{font-style:normal;color:var(--orange)}
.contact{position:absolute;top:186px;display:flex;align-items:center;gap:10px;font-size:7px}
.contact-icon{width:21px;height:21px;border-radius:50%;border:1px solid rgba(255,255,255,.4);display:flex;align-items:center;justify-content:center}
</style>
</head>
<body>

<!-- Cover -->
<section class="slide slide--cover">
  <div class="cover-logo">Velmora Quill Industries<small>Engineering AI Transformations</small></div>
  <div class="cover-name">VELMORA QUILL INDUSTRIES</div>
  <div class="cover-tag">Engineering AI Transformations for the<br>Future of Business</div>
</section>

<!-- Agenda -->
<section class="slide slide--agenda">
  <h2 class="title">Our <em>Agenda</em></h2>
  <div class="brandmark">Velmora<br>Quill</div>
  <div class="agenda-card" style="left:37px;top:47px"><div class="agenda-num">01</div><div class="agenda-head">WELCOME &amp; INTRODUCTION</div><div class="agenda-text">Who we are and our mission in<br>AI consulting</div></div>
  <div class="agenda-card" style="left:243px;top:47px"><div class="agenda-num">02</div><div class="agenda-head">INDUSTRY CHALLENGES</div><div class="agenda-text">Current pain points and where AI<br>delivers impact</div></div>
  <div class="agenda-card" style="left:37px;top:117px"><div class="agenda-num">03</div><div class="agenda-head">OUR SOLUTIONS &amp; CAPABILITIES</div><div class="agenda-text">Consulting approach, automation,<br>decision intelligence</div></div>
  <div class="agenda-card" style="left:243px;top:117px"><div class="agenda-num">04</div><div class="agenda-head">CASE STUDIES &amp; ROI</div><div class="agenda-text">Proven results from financial, mining,<br>and supply chain sectors</div></div>
  <div class="agenda-card" style="left:140px;top:187px"><div class="agenda-num">05</div><div class="agenda-head">ROADMAP &amp; NEXT STEPS</div><div class="agenda-text">How we partner for transformation<br>and execution</div></div>
  <div class="page">PAGE 2</div>
</section>

<!-- Solutions -->
<section class="slide slide--solutions">
  <h2 class="title">Solutions for the <em>Future</em></h2>
  <div class="brandmark">Velmora<br>Quill</div>
  <div class="sub">EMPOWERING AUTOMATION, INTELLIGENCE, AND TRANSFORMATION.</div>
  <div class="page">PAGE 3</div>
</section>

<!-- Why -->
<section class="slide slide--why">
  <h2 class="title">Why AI Transformation <em>Matters</em></h2>
  <div class="brandmark">Velmora<br>Quill</div>
  <div class="why-sub">DRIVING IMPACT THROUGH INTELLIGENCE</div>
  <ul class="why-list">
    <li><b>Reduce Operational Risk:</b> AI-driven insights<br>lower risk by up to 40%.</li>
    <li><b>Boost Efficiency:</b> Automation accelerates<br>workflows and decision-making.</li>
    <li><b>Data-Driven Advantage:</b> Turn raw data into<br>actionable strategies for growth.</li>
    <li><b>Scalable Innovation:</b> AI adapts as your<br>business evolves, ensuring future readiness.</li>
  </ul>
  <div class="why-photo" role="img" aria-label="Photo: team working around a table overlaid with an AI network graphic"></div>
  <div class="page">PAGE 4</div>
</section>

<!-- Compare -->
<section class="slide slide--compare">
  <h2 class="compare-title"><span>Traditional Approach vs <em>AI-Powered Approach</em></span></h2>
  <div class="brandmark">Velmora<br>Quill</div>
  <table class="compare-table">
    <thead><tr><th style="width:131px">ASPECT</th><th style="width:138px">TRADITIONAL</th><th>AI-DRIVEN</th></tr></thead>
    <tbody>
      <tr><td>DECISION SPEED</td><td>WEEKS</td><td>REAL-TIME</td></tr>
      <tr><td>ACCURACY</td><td>70%</td><td>95%</td></tr>
      <tr><td>OPERATIONAL COST</td><td>HIGH</td><td>25%</td></tr>
      <tr><td>RISK MANAGEMENT</td><td>REACTIVE</td><td>PREDICTIVE</td></tr>
    </tbody>
  </table>
  <div class="page">PAGE 5</div>
</section>

<!-- Path -->
<section class="slide slide--path">
  <h2 class="title" style="top:42px">Your Path to <em>AI-Powered Success</em></h2>
  <div class="brandmark">Velmora<br>Quill</div>
  <svg class="abs" style="left:0;top:0" width="466" height="262" viewBox="0 0 466 262" fill="none">
    <g stroke="var(--orange)" stroke-width=".8" stroke-dasharray="3 3">
      <path d="M112 86 C70 86 52 120 52 147 C52 180 80 208 112 208"/>
      <path d="M181 176 C190 195 210 208 233 208"/>
      <path d="M354 86 C390 86 414 115 414 147 C414 185 385 208 354 208"/>
    </g>
    <g fill="none" stroke="var(--orange)" stroke-width=".8"><circle cx="115" cy="86" r="3.5"/><circle cx="181" cy="176" r="3.5"/><circle cx="350" cy="208" r="3.5"/></g>
    <g stroke="var(--white)" stroke-width="1.2">
      <path d="M112 208 C150 208 172 180 175 147 C178 110 200 86 233 86"/>
      <path d="M233 208 C272 208 293 180 296 147 C299 110 320 86 354 86"/>
    </g>
    <path d="M233 82 L241 86 L233 90Z M354 82 L362 86 L354 90Z" fill="var(--white)"/>
    <g stroke="rgba(255,255,255,.5)" stroke-width=".8"><circle cx="112" cy="115" r="14"/><circle cx="233" cy="115" r="14"/><circle cx="354" cy="115" r="14"/></g>
    <g stroke="var(--white)" stroke-width=".8" fill="none">
      <rect x="106" y="109" width="11" height="11"/><circle cx="113" cy="116" r="3"/>
      <path d="M227 121 V112 H239 V121 Z M230 119 V116 M233 119 V114 M236 119 V113"/>
      <circle cx="351" cy="113" r="4"/><circle cx="358" cy="119" r="3.5"/>
    </g>
  </svg>
  <div class="step" style="left:112px;top:144px"><div class="step-head">ASSESSMENT &amp; STRATEGY</div><div class="step-text">Evaluate current processes<br>and AI readiness.</div></div>
  <div class="step" style="left:233px;top:144px"><div class="step-head">PILOT PROJECTS</div><div class="step-text">Quick wins to demonstrate<br>ROI.</div></div>
  <div class="step" style="left:354px;top:144px"><div class="step-head">SCALING &amp; INTEGRATION</div><div class="step-text">Deploy enterprise-wide AI<br>solutions.</div></div>
  <div class="page">PAGE 6</div>
</section>

<!-- Roadmap -->
<section class="slide slide--roadmap">
  <h2 class="title">Your AI Transformation <em>Roadmap</em></h2>
  <div class="brandmark">Velmora<br>Quill</div>
  <svg class="abs" style="left:0;top:0" width="466" height="262" viewBox="0 0 466 262" fill="none">
    <path d="M127 211 C135 192 150 187 168 187 H305" stroke="var(--line)" stroke-width=".8"/>
    <path d="M305 187 H345 C365 187 374 172 374 158 C374 140 362 127 345 127 H130 C113 127 99 115 99 98 C99 80 113 67 130 67 H345 C360 67 372 56 373 44" stroke="var(--line)" stroke-width=".8"/>
    <g fill="var(--blue-deep)" stroke="var(--white)" stroke-width=".8">
      <circle cx="168" cy="67" r="4.5"/><circle cx="236" cy="67" r="4.5"/><circle cx="305" cy="67" r="4.5"/>
      <circle cx="168" cy="127" r="4.5"/><circle cx="236" cy="127" r="4.5"/><circle cx="305" cy="127" r="4.5"/>
      <circle cx="168" cy="187" r="4.5"/><circle cx="236" cy="187" r="4.5"/><circle cx="305" cy="187" r="4.5"/>
      <circle cx="99" cy="98" r="4.5"/><circle cx="374" cy="158" r="4.5"/>
    </g>
    <g fill="var(--orange)">
      <circle cx="168" cy="67" r="2.3"/><circle cx="236" cy="67" r="2.3"/><circle cx="305" cy="67" r="2.3"/>
      <circle cx="168" cy="127" r="2.3"/><circle cx="236" cy="127" r="2.3"/><circle cx="305" cy="127" r="2.3"/>
      <circle cx="168" cy="187" r="2.3"/><circle cx="236" cy="187" r="2.3"/><circle cx="305" cy="187" r="2.3"/>
    </g>
    <g fill="var(--white)"><circle cx="99" cy="98" r="2.3"/><circle cx="374" cy="158" r="2.3"/></g>
    <g stroke="var(--white)" stroke-width=".8"><circle cx="373" cy="35" r="7"/><circle cx="373" cy="35" r="4"/><circle cx="373" cy="35" r="1.2" fill="var(--orange)"/><path d="M373 35 L381 27"/></g>
    <path d="M96 222 L104 206 L106 216 Z M99 212 L93 214 M101 218 L99 224" stroke="var(--orange)" stroke-width=".8"/>
  </svg>
  <div class="tl" style="left:54px;top:83px"><div class="tl-year">2021</div><div class="tl-text">Sed ut perspiciatis unde<br>omnis iste natus error sit</div></div>
  <div class="tl" style="left:168px;top:77px"><div class="tl-year">2022</div><div class="tl-text">Sed ut perspiciatis unde<br>omnis iste natus error sit</div></div>
  <div class="tl" style="left:236px;top:77px"><div class="tl-year">2023</div><div class="tl-text">Sed ut perspiciatis unde<br>omnis iste natus error sit</div></div>
  <div class="tl" style="left:305px;top:77px"><div class="tl-year">2024</div><div class="tl-text">Sed ut perspiciatis unde<br>omnis iste natus error sit</div></div>
  <div class="tl" style="left:168px;top:134px"><div class="tl-year">2020</div><div class="tl-text">Sed ut perspiciatis unde<br>omnis iste natus error sit</div></div>
  <div class="tl" style="left:236px;top:134px"><div class="tl-year">2019</div><div class="tl-text">Sed ut perspiciatis unde<br>omnis iste natus error sit</div></div>
  <div class="tl" style="left:305px;top:134px"><div class="tl-year">2018</div><div class="tl-text">Sed ut perspiciatis unde<br>omnis iste natus error sit</div></div>
  <div class="tl" style="left:411px;top:146px"><div class="tl-year">2017</div><div class="tl-text">Sed ut perspiciatis unde<br>omnis iste natus error sit</div></div>
  <div class="tl" style="left:168px;top:196px"><div class="tl-year">2014</div><div class="tl-text">Sed ut perspiciatis unde<br>omnis iste natus error sit</div></div>
  <div class="tl" style="left:236px;top:196px"><div class="tl-year">2015</div><div class="tl-text">Sed ut perspiciatis unde<br>omnis iste natus error sit</div></div>
  <div class="tl" style="left:305px;top:196px"><div class="tl-year">2016</div><div class="tl-text">Sed ut perspiciatis unde<br>omnis iste natus error sit</div></div>
  <div class="page">PAGE 7</div>
</section>

<!-- Thank you -->
<section class="slide slide--thanks">
  <div class="thanks-logo">Velmora Quill Industries<small>Engineering AI Transformations</small></div>
  <div class="thanks-big">THANK <em>YOU</em></div>
  <div class="contact" style="left:103px">
    <span class="contact-icon"><svg width="9" height="9" viewBox="0 0 24 24" fill="var(--white)"><path d="M6.6 10.8a15 15 0 0 0 6.6 6.6l2.2-2.2c.3-.3.7-.4 1-.2 1.1.4 2.3.6 3.6.6.6 0 1 .4 1 1V20c0 .6-.4 1-1 1C10.6 21 3 13.4 3 4c0-.6.4-1 1-1h3.5c.6 0 1 .4 1 1 0 1.3.2 2.5.6 3.6.1.3 0 .7-.2 1z"/></svg></span>
    +1 (555) 014-2290
  </div>
  <div class="contact" style="left:253px">
    <span class="contact-icon"><svg width="9" height="9" viewBox="0 0 24 24" fill="var(--white)"><path d="M3 5h18v14H3z M3 5l9 7 9-7" stroke="var(--blue-deep)" stroke-width="1.5"/></svg></span>
    INFO@VELMORAQUILL.AI
  </div>
</section>

</body>
</html>
```